House flipping business web site needed

pinecrestholdingsgroup.example.
I am a residential developer in Northern NJ and I am looking for a fresh new updated website. I have an intro video about my company being made now. I don't update it very often but I want an easy format that I can add update photos to on projects I have worked on or homes I renovate for sale.

Target Market(s)

investors into my projects so a portfolio , people looking to sell their homes to me.

Industry/Entity Type

Real Estate Development

Number of Pages Required

4 page

Font styles to use
Serif

Colors
33b8a4
39a9d7
cadf82

Requirements
Must have
• space for an intro video about my company
• a portfolio with pictures and information about each project
• Markets we serve- Morris County, NJ
• My logo- already created
• SEO
• Yes I would like this to function over all platforms. Phone, computer, all platforms.
• history and background page
• I am looking for a completed page that I can upload to the site that hosts my website
Nice to have
• I want something creative, easy to navigate. modern.

```html
<!DOCTYPE html>
<html lang="en">
<head>
<meta charset="utf-8">
<title>Pinecrest Holdings Group</title>
<link href="https://fonts.googleapis.com/css2?family=Cinzel:wght@400;700&family=Open+Sans:ital,wght@0,400;0,600;0,700;1,600&display=swap" rel="stylesheet">
<style>
:root{
  --teal:#33b8a4;
  --sky:#39a9d7;
  --sky-deep:#1f8fc6;
  --lime:#cadf82;
  --ink:#222;
  --text:#666;
  --topbar:#f4f5f6;
  --footer:#1d1d1d;
  --footer-text:#cfcfcf;
}
*{margin:0;padding:0;box-sizing:border-box}
html,body{width:726px;height:1200px;overflow:hidden;background:#fff}
body{position:relative;font-family:"Open Sans",sans-serif;color:var(--text)}
.abs{position:absolute}
.serif{font-family:"Cinzel",serif}

/* top bar */
.topbar{left:0;top:0;width:726px;height:47px;background:var(--topbar)}
.contact-chip{top:16px;display:flex;align-items:center;gap:8px;font-size:10px;color:var(--ink);font-weight:600}
.chip-icon{width:13px;height:13px;border-radius:3px;display:flex;align-items:center;justify-content:center}
.social-top{right:61px;top:17px;display:flex;gap:5px}
.social-top span{width:15px;height:15px;border:1px solid var(--teal);border-radius:50%}

/* nav */
.nav{left:0;top:47px;width:726px;height:32px;background:linear-gradient(#4bb9e6,var(--sky-deep))}
.nav a{position:absolute;top:0;height:32px;line-height:32px;color:#fff;font-size:8.5px;text-decoration:none;text-transform:uppercase;letter-spacing:.2px}
.nav a.active{background:#2284bb;padding:0 15px}
.brand-badge{left:308px;top:0;width:110px;height:93px;background:#fff;border-radius:0 0 50px 50px/0 0 22px 22px;box-shadow:0 2px 4px rgba(0,0,0,.15);display:flex;align-items:center;justify-content:center;text-align:center}
.brand-badge span{font-family:"Cinzel",serif;font-size:13px;line-height:1.15;color:var(--sky-deep);font-weight:400}

/* hero */
.hero{left:0;top:79px;width:726px;height:249px;background:linear-gradient(180deg,#2b3a2a 0%,#55624f 45%,#3d5a2c 80%,#4e6f2f 100%)}
.hero-title{left:0;width:726px;top:72px;text-align:center;color:#fff;font-size:36px;font-weight:400;white-space:nowrap;text-shadow:0 2px 4px rgba(0,0,0,.4)}
.hero-sub{left:0;width:726px;top:116px;text-align:center;color:#fff;font-size:14.5px;font-style:italic;font-weight:600;text-shadow:0 1px 3px rgba(0,0,0,.5)}
.btn-hero{left:302px;top:144px;width:121px;height:26px;background:var(--teal);color:#fff;font-size:9px;font-weight:700;display:flex;align-items:center;justify-content:center;border-radius:2px}
.hero-arrow{top:97px}

/* welcome */
.welcome-title{left:60px;top:358px;width:300px;color:var(--ink);font-size:13px;letter-spacing:.2px;white-space:nowrap}
.body-copy{font-size:7px;line-height:14.5px;color:var(--text)}
.btn-outline{left:60px;top:508px;width:69px;height:22px;border:1px solid #bbb;border-radius:3px;color:var(--teal);font-size:7.5px;font-weight:700;display:flex;align-items:center;justify-content:center}
.video{left:376px;top:350px;width:289px;height:188px;background:linear-gradient(180deg,#6f8e4f 0%,#8aa06b 30%,#4f6f7c 55%,#6d8b93 80%,#7a7260 100%)}
.video-bar{left:0;top:0;width:289px;height:21px;background:rgba(20,20,20,.85);color:#fff;font-size:9px;font-weight:600;padding:5px 11px}
.play{left:129px;top:84px;width:30px;height:30px;border-radius:50%;background:#111;display:flex;align-items:center;justify-content:center}

/* markets */
.markets{left:0;top:565px;width:726px;height:210px;background:linear-gradient(90deg,#3aa5d6,#56b4df 50%,#3ea7d8)}
.markets-title{left:0;width:726px;top:26px;text-align:center;color:#fff;font-size:14px;letter-spacing:.6px}
.market-photo{width:147px;height:114px;border:2px solid #fff}
.market-name{color:#fff;font-size:10px;font-weight:700}
.market-text{color:#eaf6fc;font-size:7px;line-height:12.5px;width:130px}
.market-more{color:#fff;font-size:7.5px;font-weight:700}

/* portfolio */
.portfolio-title{left:0;width:726px;top:800px;text-align:center;color:var(--ink);font-size:15px;letter-spacing:.5px}
.project{top:831px;width:143px;text-align:center}
.project-photo{width:143px;height:107px}
.project-name{margin-top:9px;font-size:10px;font-weight:700;color:var(--ink)}
.project-text{margin-top:6px;font-size:7px;line-height:12.5px;color:var(--text)}
.portfolio-arrow{top:877px}

/* footer */
.footer{left:0;top:1017px;width:726px;height:183px;background:var(--footer);border-top:3px solid var(--sky)}
.footer-brand{left:70px;top:50px;width:140px;font-family:"Cinzel",serif;font-size:17px;line-height:1.2;color:var(--sky);text-align:center}
.f-head{color:#fff;font-size:10.5px;letter-spacing:.5px;top:20px}
.f-links{top:48px;font-size:7.5px;line-height:17.5px;color:var(--footer-text)}
.f-copy{font-size:7px;line-height:12px;color:var(--footer-text)}
.email-field{left:354px;top:73px;width:148px;height:19px;background:#fff;font-size:7px;color:#888;padding:5px 9px}
.btn-sub{left:354px;top:101px;width:61px;height:21px;border:1px solid #fff;border-radius:2px;color:#fff;font-size:7.5px;font-weight:700;display:flex;align-items:center;justify-content:center}
.f-rule{left:60px;top:139px;width:606px;height:1px;background:#333}
.copyright{left:60px;top:155px;font-size:7px;color:var(--footer-text)}
.social-foot{left:575px;top:150px;display:flex;gap:4px}
.social-foot span{width:20px;height:20px;border:1.5px solid #fff;border-radius:50%}
</style>
</head>
<body>

<!-- top bar -->
<div class="abs topbar"></div>
<div class="abs contact-chip" style="left:60px">
  <span class="chip-icon" style="background:var(--teal)">
    <svg width="8" height="8" viewBox="0 0 24 24"><path fill="#fff" d="M6.6 10.8a15 15 0 0 0 6.6 6.6l2.2-2.2c.3-.3.7-.4 1-.2 1.1.4 2.3.6 3.6.6.6 0 1 .4 1 1V20c0 .6-.4 1-1 1A17 17 0 0 1 3 4c0-.6.4-1 1-1h3.5c.6 0 1 .4 1 1 0 1.3.2 2.5.6 3.6.1.3 0 .7-.2 1z"/></svg>
  </span>+1 555-014-2290
</div>
<div class="abs contact-chip" style="left:174px">
  <span class="chip-icon" style="background:var(--lime)">
    <svg width="8" height="6" viewBox="0 0 16 12"><rect x="0.5" y="0.5" width="15" height="11" fill="none" stroke="#fff"/><path d="M1 1l7 6 7-6" fill="none" stroke="#fff"/></svg>
  </span>@pinecrestholdings
</div>
<div class="abs social-top"><span></span><span></span><span></span><span></span><span></span><span></span></div>

<!-- navigation -->
<nav class="abs nav">
  <a class="active" style="left:59px">Home</a>
  <a style="left:125px">About Us</a>
  <a style="left:190px">Services</a>
  <a style="left:250px">Blog</a>
  <a style="left:447px">Portfolio</a>
  <a style="left:517px">Testimonial</a>
  <a style="left:595px">Contact &nbsp;&nbsp;|</a>
  <svg class="abs" style="left:658px;top:12px" width="8" height="8" viewBox="0 0 10 10"><circle cx="4" cy="4" r="3" fill="none" stroke="#fff" stroke-width="1.4"/><path d="M6.2 6.2L9 9" stroke="#fff" stroke-width="1.4"/></svg>
</nav>
<div class="abs brand-badge"><span>PINECREST<br>HOLDINGS GROUP</span></div>

<!-- hero -->
<section class="abs hero" role="img" aria-label="Photo of a weathered cottage in a wooded yard">
  <h1 class="abs hero-title serif">Pinecrest Holdings Group</h1>
  <p class="abs hero-sub">We are into house flipping business in New Jersey.</p>
  <div class="abs btn-hero">GET MORE INFO &gt;&gt;</div>
  <svg class="abs hero-arrow" style="left:20px" width="12" height="52" viewBox="0 0 12 52"><path d="M11 1L1 26l10 25" fill="none" stroke="#fff" stroke-width="1"/></svg>
  <svg class="abs hero-arrow" style="left:694px" width="12" height="52" viewBox="0 0 12 52"><path d="M1 1l10 25L1 51" fill="none" stroke="#fff" stroke-width="1"/></svg>
</section>

<!-- welcome -->
<h2 class="abs welcome-title serif">Welcome to Pinecrest Holdings Group</h2>
<p class="abs body-copy" style="left:60px;top:384px;width:298px">We are a team of experienced home buyers and renovators in the Morris County, NJ area. Our specialty is purchasing distressed homes and property.</p>
<p class="abs body-copy" style="left:60px;top:424px;width:298px">&nbsp;We then collaborate with the best talents in Northern New Jersey to renovate those properties and transform them into the best house in the neighborhood. As a result we create equity, a return on investment and most importantly we give home buyers a worry free property that provides a better way of life and hope for their future. We only work in the Morris County area so we are local.</p>
<div class="abs btn-outline">READ MORE &gt;&gt;</div>

<div class="abs video" role="img" aria-label="Intro video still of a calm lake framed by trees">
  <div class="abs video-bar">Pinecrest Holdings Group</div>
  <svg class="abs" style="left:256px;top:6px" width="24" height="10" viewBox="0 0 24 10"><circle cx="5" cy="5" r="4" fill="none" stroke="#fff" stroke-width="1.3"/><path d="M5 3v2.5h2" stroke="#fff" stroke-width="1.1" fill="none"/><path d="M14 9c0-4 3-5 7-5M18 1l3 3-3 3" stroke="#fff" stroke-width="1.5" fill="none"/></svg>
  <div class="abs play"><svg width="10" height="11" viewBox="0 0 10 11"><path d="M1 0l9 5.5L1 11z" fill="#fff"/></svg></div>
</div>

<!-- markets -->
<section class="abs markets">
  <h2 class="abs markets-title serif">Markets We Serve</h2>
  <div class="abs market-photo" style="left:60px;top:68px;background:linear-gradient(160deg,#9ec3e3 0%,#c9b98a 40%,#d48a3a 65%,#3f88b8 100%)" role="img" aria-label="Photo of an old stone mill by a pond in autumn"></div>
  <h3 class="abs market-name" style="left:221px;top:66px">Morris County</h3>
  <p class="abs market-text" style="left:221px;top:86px">We only buy and renovate homes in our neighborhoods right here in the Morris County, NJ area. Is a house in your neighborhood an eyesore? Is it vacant, boarded up and a hazard to the neighborhood..</p>
  <div class="abs market-more" style="left:221px;top:171px">READ MORE &gt;&gt;</div>
  <div class="abs market-photo" style="left:379px;top:68px;background:linear-gradient(180deg,#6d6d96 0%,#d99c8c 35%,#4e5f8f 60%,#2a3050 100%)" role="img" aria-label="Photo of a city skyline over water at dusk"></div>
  <h3 class="abs market-name" style="left:539px;top:66px">New Jersey</h3>
  <p class="abs market-text" style="left:539px;top:86px">We only buy and renovate homes in our neighborhoods right here in the Morris County, NJ area. Is a house in your neighborhood an eyesore? Is it vacant, boarded up and a hazard to the neighborhood..</p>
  <div class="abs market-more" style="left:539px;top:171px">READ MORE &gt;&gt;</div>
</section>

<!-- portfolio -->
<h2 class="abs portfolio-title serif">Our Portfolio</h2>
<svg class="abs portfolio-arrow" style="left:42px" width="9" height="16" viewBox="0 0 9 16"><path d="M8 1L1 8l7 7" fill="none" stroke="#aaa" stroke-width="1.5"/></svg>
<svg class="abs portfolio-arrow" style="left:675px" width="9" height="16" viewBox="0 0 9 16"><path d="M1 1l7 7-7 7" fill="none" stroke="#aaa" stroke-width="1.5"/></svg>

<article class="abs project" style="left:60px">
  <div class="project-photo" style="background:linear-gradient(180deg,#c9c7c4 0%,#a89a85 50%,#6e5a45 100%)" role="img" aria-label="Photo of a renovated two-storey home in Rockaway"></div>
  <h3 class="project-name">Rockaway, NJ</h3>
  <p class="project-text">Many upgrades to this home, Added a new full bath, family room, office,</p>
</article>
<article class="abs project" style="left:214px">
  <div class="project-photo" style="background:linear-gradient(180deg,#7c9e5a 0%,#c8c3b5 45%,#9c9a8e 70%,#5f7f3c 100%)" role="img" aria-label="Photo of a rebuilt colonial home in Denville"></div>
  <h3 class="project-name">Denville, NJ</h3>
  <p class="project-text">House was torn down. Using portions of the foundation and an existing</p>
</article>
<article class="abs project" style="left:369px">
  <div class="project-photo" style="background:linear-gradient(180deg,#3f5a35 0%,#6e8fa0 45%,#5c7d3f 75%,#6a9b3c 100%)" role="img" aria-label="Photo of a remodeled blue cottage in Boonton"></div>
  <h3 class="project-name">Boonton, NJ</h3>
  <p class="project-text">A complete remodel and add on to this 2 bedroom house.</p>
</article>
<article class="abs project" style="left:523px">
  <div class="project-photo" style="background:linear-gradient(180deg,#8aa06a 0%,#c7cbcf 40%,#8d877c 70%,#6e8a43 100%)" role="img" aria-label="Photo of a home with stone retaining wall in Rockaway"></div>
  <h3 class="project-name">Rockaway, NJ</h3>
  <p class="project-text">Radiant heat installed in basement and first floor bathroom, office</p>
</article>

<!-- footer -->
<footer class="abs footer">
  <div class="abs footer-brand">PINECREST<br>HOLDINGS GROUP</div>

  <h4 class="abs f-head serif" style="left:251px">Information</h4>
  <div class="abs f-links" style="left:251px">Home<br>About<br>Contact<br>Portfolio</div>

  <h4 class="abs f-head serif" style="left:354px">Newsletter</h4>
  <p class="abs f-copy" style="left:354px;top:48px;width:150px">Register your email address to get information about us</p>
  <div class="abs email-field">Email Address</div>
  <div class="abs btn-sub">SUBSCRIBE</div>

  <h4 class="abs f-head serif" style="left:538px">Contact Us</h4>
  <svg class="abs" style="left:538px;top:49px" width="6" height="9" viewBox="0 0 6 9"><path d="M3 0a3 3 0 0 1 3 3c0 2-3 6-3 6S0 5 0 3a3 3 0 0 1 3-3z" fill="#fff"/><circle cx="3" cy="3" r="1" fill="#1d1d1d"/></svg>
  <p class="abs f-copy" style="left:558px;top:49px">Pinecrest Holdings Group<br>Morris County, NJ</p>
  <svg class="abs" style="left:538px;top:89px" width="8" height="8" viewBox="0 0 24 24"><path fill="#fff" d="M6.6 10.8a15 15 0 0 0 6.6 6.6l2.2-2.2c.3-.3.7-.4 1-.2 1.1.4 2.3.6 3.6.6.6 0 1 .4 1 1V20c0 .6-.4 1-1 1A17 17 0 0 1 3 4c0-.6.4-1 1-1h3.5c.6 0 1 .4 1 1 0 1.3.2 2.5.6 3.6.1.3 0 .7-.2 1z"/></svg>
  <p class="abs f-copy" style="left:558px;top:87px">+1 555-014-2290</p>
  <svg class="abs" style="left:538px;top:115px" width="9" height="7" viewBox="0 0 16 12"><rect width="16" height="12" fill="#fff"/><path d="M0 0l8 6 8-6" fill="none" stroke="#1d1d1d" stroke-width="1.5"/></svg>
  <p class="abs f-copy" style="left:558px;top:113px">info@pinecrestholdingsgroup.example</p>

  <div class="abs f-rule"></div>
  <p class="abs copyright">Copyrights © 2016, Pinecrest Holdings Group. All rights reserved.</p>
  <div class="abs social-foot"><span></span><span></span><span></span><span></span></div>
</footer>

</body>
</html>
```